Large online photo magazine needs redesign

We have previously digitised a historical photographic magazine of around 20,000 printed pages and made it available online. The magazine ran up to the early 1970s, and the content is largely black and white photographs of local events, accompanied by short captions.

Although the content is very rich, the design needs to be revisited so that:
* it is visually appealing
* it is responsive (i.e. works in browsers across all manner of devices)
* is faithful to the nature of the content

There are only a few core page types, and the central one is the article page, an example of which can be seen at:
http://snapgazette.example/gisborne/issue/KLR48_19600714/t1-body-d4.html

Any design submitted should be based on the treatment of an article page such as the above.

Given the large number of pages on our site, we need a design which can be templated to work for any content in the collection, i.e. we cannot hand-craft our templates to match a given page of content, rather a template must work acceptably well for all content.

The current site, although basic in design, has the advantage that it is quite efficient in the amount of data per page request (around 100k - 200k). While not adverse to web fonts, banner imagery etc, we will carefully consider the benefit gained from any such treatment against the amount of extra data that needs to be downloaded to the client's browser.

For the right design, we are able ourselves to adapt it to a CSS layout.

An example of each core page type is as follows (though for this project we only expect a design for a single page, as itemised above):

http://snapgazette.example/gisborne/index.html
http://snapgazette.example/gisborne/about.html
http://snapgazette.example/gisborne/help.html
http://snapgazette.example/gisborne/initial/index.html
http://snapgazette.example/gisborne/search/results?type=section&text=smith&cmdSubmit=Go
http://snapgazette.example/gisborne/advanced-search/index.html
http://snapgazette.example/gisborne/issue/KLR48_19600714/t1-front-d1.html
http://snapgazette.example/gisborne/issue/KLR48_19600714/index.html
http://snapgazette.example/gisborne/issue/KLR48_19600714/fig-KLR48_19600714_005a.html
http://snapgazette.example/gisborne/issue/KLR48_19600714/KLR48_19600714_012.html
http://snapgazette.example/gisborne/issue/KLR48_19600714/thumbnails.html

Target Market(s)

A general browsing audience of all ages, but skewed towards the older generations, and those interested in family / regional history.

The average user will not be particularly web-savy, and the treatment of the content should not detract / distract from the actual content itself.

Industry/Entity Type

Events

Requirements
Must have
• * it is visually appealing
The content should be visually appealing to the audience, which can be defined as a general browsing audience of all ages, but skewed towards the middle and older generations.

* it is responsive (the design can be adapted - by us - to work in browsers across all manner of devices)

The magazine covers (http://snapgazette.example/gisborne/issues/index.html) offer some possible inspiration for treatment of the material.

```html
<!DOCTYPE html>
<html lang="en">
<head>
<meta charset="utf-8">
<title>Flying Sisters from Gisborne – Gisborne Snap Gazette</title>
<link rel="stylesheet" href="https://fonts.googleapis.com/css2?family=PT+Sans:wght@400;700&family=Arimo:wght@400;700&display=swap">
<style>
:root{
  --brand:#cc3d52;
  --brand-dark:#3b1c24;
  --nav:#585c60;
  --nav-line:#4a4d51;
  --footer:#6a6a6a;
  --page:#f3f3f3;
  --card:#ffffff;
  --ink:#2b2b2b;
  --muted:#555;
  --rule:#e2e2e2;
  --hatch:#d4d4d4;
}
*{box-sizing:border-box;margin:0;padding:0}
html,body{width:1072px;height:1200px;overflow:hidden}
body{position:relative;background:var(--page);font-family:"Arimo",Arial,sans-serif;color:var(--ink)}
a{color:inherit;text-decoration:none}

.masthead{position:absolute;left:0;top:0;width:1072px;height:76px;background:var(--brand);border-top:3px solid var(--brand-dark)}
.masthead .brand{position:absolute;left:127px;top:20px;font-family:"PT Sans",sans-serif;font-weight:700;font-size:30px;color:#fff;letter-spacing:.5px}

.utility{position:absolute;left:0;top:76px;width:1072px;height:58px;background:#fff}
.breadcrumb{position:absolute;left:127px;top:19px;font-size:11px;color:var(--brand)}
.search{position:absolute;left:678px;top:17px;width:268px;height:25px;border:1px solid #ddd;display:flex;background:#fff}
.search input{flex:1;border:0;font:10.5px "Arimo",sans-serif;color:#666;padding-left:6px;background:transparent}
.search button{width:28px;border:0;border-left:1px solid #ddd;background:#fafafa;font:10.5px "Arimo",sans-serif;color:#666}

.mainnav{position:absolute;left:0;top:134px;width:1072px;height:33px;background:var(--nav)}
.mainnav ul{list-style:none;position:absolute;left:126px;top:0;display:flex;height:33px}
.mainnav li{height:33px;display:flex;align-items:center;justify-content:center;color:#fff;font-weight:700;font-size:10.5px;letter-spacing:.3px;border-right:1px solid var(--nav-line);position:relative}
.mainnav li.current{background:var(--brand)}
.mainnav li.current::after{content:"";position:absolute;bottom:-6px;left:50%;margin-left:-5px;border:5px solid transparent;border-top-color:var(--brand);border-bottom:0;border-top-width:6px}

.card{position:absolute;left:126px;top:193px;width:820px;height:912px;background:var(--card);border:1px solid #e4e4e4;box-shadow:0 1px 3px rgba(0,0,0,.08)}
.article{position:relative;height:204.4px}
.article h2{position:absolute;left:9px;top:5px;font-family:"PT Sans",sans-serif;font-weight:400;font-size:18px;color:var(--brand)}
.hatch{position:absolute;left:6px;width:808px;height:5px;background:repeating-linear-gradient(120deg,var(--hatch) 0 1px,transparent 1px 3px)}
.hatch.top{top:34px}
.hatch.bottom{top:198px}
.plate{position:absolute;left:6px;top:51px;width:137px;height:134px}
.caption{position:absolute;left:153px;top:52px;width:661px;font-size:10.4px;line-height:16.75px;text-align:justify;hyphens:auto;color:var(--ink)}
.lead{position:absolute;left:153px;top:122px;font-family:"PT Sans",sans-serif;font-weight:700;font-size:11.5px;color:var(--brand)}
.meta{position:absolute;left:150px;top:154px;width:670px;height:32px;border-top:1px solid var(--rule);border-bottom:1px solid var(--rule);font-size:10.4px;font-weight:700;color:#333}
.meta .date{position:absolute;left:52px;top:9px;display:flex;align-items:center;gap:6px}
.meta .comment{position:absolute;left:468px;top:8px;display:flex;align-items:center;gap:9px}

.pager{position:absolute;left:8px;top:853px;display:flex;gap:8.5px}
.pager a{height:25px;min-width:25px;padding:0 6px;border:1px solid #ddd;background:linear-gradient(#fff,#f1f1f1);font-family:"PT Sans",sans-serif;font-weight:700;font-size:12.5px;color:#555;display:flex;align-items:center;justify-content:center}
.pager a.wide{width:50px}
.issue-nav{position:absolute;left:539px;top:851px;width:270px;height:39px;border:1px solid #e2e2e2;box-shadow:0 1px 2px rgba(0,0,0,.08);display:flex;align-items:center;justify-content:center;gap:10px;font-family:"PT Sans",sans-serif;font-weight:700;font-size:11.5px;color:var(--brand)}

.sitefoot{position:absolute;left:0;top:1130px;width:1072px;height:70px;background:var(--footer);color:#fff}
.licence{position:absolute;left:171px;top:10px;width:74px;height:25px;background:#fff;border:2px solid #222}
.copyright{position:absolute;left:127px;top:42px;font-family:"PT Sans",sans-serif;font-weight:700;font-size:11.5px}
.social{position:absolute;top:23px;width:24px;height:24px;border-radius:50%}
.code{position:absolute;left:979px;top:28px;font-size:11px;color:#eee}
</style>
</head>
<body>

<header class="masthead"><a class="brand" href="#">Gisborne Snap Gazette</a></header>

<div class="utility">
  <nav class="breadcrumb">Gisborne Snap Gazette &gt; Issues &gt; KLR48_19600714 &gt; t1-body-d4</nav>
  <form class="search"><input type="text" value="Search Gisborne Snap Gazette" aria-label="Search"><button type="button">Go</button></form>
</div>

<nav class="mainnav">
  <ul>
    <li class="current" style="width:85px">HOME</li>
    <li style="width:69px">ABOUT</li>
    <li style="width:216px">BROWSE GISBORNE SNAP GAZETTE</li>
    <li style="width:105px">A-Z PEOPLE</li>
    <li style="width:98px">ADVANCED</li>
    <li style="width:112px">SEARCHHELP</li>
    <li style="width:135px;border-right:0">REPORT AN ERROR</li>
  </ul>
</nav>

<main class="card">
  <article class="article">
    <h2>Flying Sisters from Gisborne</h2><div class="hatch top"></div>
    <div class="plate" role="img" aria-label="Scanned page photo of a river bridge with caption text" style="background:linear-gradient(#e6e2d6,#9a968c 60%,#cfcbc0)"></div>
    <p class="caption">This is probably something of a record--three sisters who are all air hostesses. They are the Harlow sisters.....Marguerite, Elsie, and Rosalind, daughters of Mr and Mrs R. T. Harlow, Wexley Road, Gisborne.And this young lady, Doreen Pettit, of Auckland, has made history in another way. Gisborne, on Sunday of last week. Hostess service has been extended by C.A.S. to include Gisborne flights, beginning with the Sunday Services.</p>
    <p class="lead">This is probably something of a record--three sisters who are all air hostesses.</p>
    <div class="meta"><span class="date"><svg width="16" height="16" viewBox="0 0 16 16"><circle cx="8" cy="8" r="6.5" fill="#eee" stroke="#777" stroke-width="1.3"/><path d="M8 4v4l-2 2" stroke="#777" stroke-width="1.3" fill="none"/></svg>73 July 14, 1960</span><span class="comment"><svg width="22" height="18" viewBox="0 0 22 18"><path d="M1 1h20v12H8l-4 4v-4H1z" fill="#eee" stroke="#ccc"/></svg>Leave a Comment</span></div>
    <div class="hatch bottom"></div>
  </article>
  <article class="article">
    <h2>Flying Sisters from Gisborne</h2><div class="hatch top"></div>
    <div class="plate" role="img" aria-label="Black and white photo of three air hostesses in uniform" style="background:linear-gradient(135deg,#8a8a8a,#2e2e2e 70%)"></div>
    <p class="caption">This is probably something of a record--three sisters who are all air hostesses. They are the Harlow sisters.....Marguerite, Elsie, and Rosalind, daughters of Mr and Mrs R. T. Harlow, Wexley Road, Gisborne.And this young lady, Doreen Pettit, of Auckland, has made history in another way. Gisborne, on Sunday of last week. Hostess service has been extended by C.A.S. to include Gisborne flights, beginning with the Sunday Services.</p>
    <p class="lead">This is probably something of a record--three sisters who are all air hostesses.</p>
    <div class="meta"><span class="date"><svg width="16" height="16" viewBox="0 0 16 16"><circle cx="8" cy="8" r="6.5" fill="#eee" stroke="#777" stroke-width="1.3"/><path d="M8 4v4l-2 2" stroke="#777" stroke-width="1.3" fill="none"/></svg>73 July 14, 1960</span><span class="comment"><svg width="22" height="18" viewBox="0 0 22 18"><path d="M1 1h20v12H8l-4 4v-4H1z" fill="#eee" stroke="#ccc"/></svg>Leave a Comment</span></div>
    <div class="hatch bottom"></div>
  </article>
  <article class="article">
    <h2>Flying Sisters from Gisborne</h2><div class="hatch top"></div>
    <div class="plate" role="img" aria-label="Full magazine page spread with portrait photos and captions" style="background:linear-gradient(90deg,#5a5a5a,#d9ceb0 45%,#e2d7b8 55%,#4e4e4e)"></div>
    <p class="caption">This is probably something of a record--three sisters who are all air hostesses. They are the Harlow sisters.....Marguerite, Elsie, and Rosalind, daughters of Mr and Mrs R. T. Harlow, Wexley Road, Gisborne.And this young lady, Doreen Pettit, of Auckland, has made history in another way. Gisborne, on Sunday of last week. Hostess service has been extended by C.A.S. to include Gisborne flights, beginning with the Sunday Services.</p>
    <p class="lead">This is probably something of a record--three sisters who are all air hostesses.</p>
    <div class="meta"><span class="date"><svg width="16" height="16" viewBox="0 0 16 16"><circle cx="8" cy="8" r="6.5" fill="#eee" stroke="#777" stroke-width="1.3"/><path d="M8 4v4l-2 2" stroke="#777" stroke-width="1.3" fill="none"/></svg>73 July 14, 1960</span><span class="comment"><svg width="22" height="18" viewBox="0 0 22 18"><path d="M1 1h20v12H8l-4 4v-4H1z" fill="#eee" stroke="#ccc"/></svg>Leave a Comment</span></div>
    <div class="hatch bottom"></div>
  </article>
  <article class="article">
    <h2>Flying Sisters from Gisborne</h2><div class="hatch top"></div>
    <div class="plate" role="img" aria-label="Black and white photo of an air hostess in an aircraft doorway" style="background:linear-gradient(160deg,#3a3a3a,#8c8c8c 50%,#2a2a2a)"></div>
    <p class="caption">This is probably something of a record--three sisters who are all air hostesses. They are the Harlow sisters.....Marguerite, Elsie, and Rosalind, daughters of Mr and Mrs R. T. Harlow, Wexley Road, Gisborne.And this young lady, Doreen Pettit, of Auckland, has made history in another way. Gisborne, on Sunday of last week. Hostess service has been extended by C.A.S. to include Gisborne flights, beginning with the Sunday Services.</p>
    <p class="lead">This is probably something of a record--three sisters who are all air hostesses.</p>
    <div class="meta"><span class="date"><svg width="16" height="16" viewBox="0 0 16 16"><circle cx="8" cy="8" r="6.5" fill="#eee" stroke="#777" stroke-width="1.3"/><path d="M8 4v4l-2 2" stroke="#777" stroke-width="1.3" fill="none"/></svg>73 July 14, 1960</span><span class="comment"><svg width="22" height="18" viewBox="0 0 22 18"><path d="M1 1h20v12H8l-4 4v-4H1z" fill="#eee" stroke="#ccc"/></svg>Leave a Comment</span></div>
    <div class="hatch bottom"></div>
  </article>

  <nav class="pager">
    <a class="wide" href="#">Prev</a><a href="#">1</a><a href="#">2</a><a href="#">3</a><a href="#">4</a><a href="#">5</a><a href="#">6</a><a href="#">…</a><a href="#">22</a><a class="wide" href="#">Next</a>
  </nav>
  <nav class="issue-nav"><a href="#">Previous article</a><span>|</span><a href="#">Issue contents</a><span>|</span><a href="#">Next article</a></nav>
</main>

<footer class="sitefoot">
  <div class="licence" role="img" aria-label="Licence badge"></div>
  <p class="copyright">© 2012 Eastbay Memorial Archive</p>
  <span class="social" style="left:861px;background:#3b5998" aria-label="Social link"></span>
  <span class="social" style="left:891px;background:#1da1f2" aria-label="Social link"></span>
  <span class="social" style="left:922px;background:#f57d00" aria-label="Social link"></span>
  <span class="code">C1</span>
</footer>

</body>
</html>
```